Realty Group Needs Classy, Contemporary Letterhead Design

We need a letterhead design for a new realty company located in NY, USA. We buy investment properties to rehabilitate and or keep in our rental portfolio.

```html
<!DOCTYPE html>
<html lang="en">
<head>
<meta charset="UTF-8">
<title>Holloway Realty Group – Letterhead</title>
<link href="https://fonts.googleapis.com/css2?family=Poppins:wght@400;500;700&family=Didact+Gothic&display=swap" rel="stylesheet">
<style>
  :root {
    --brand-purple: #4b2a88;
    --ink: #2b2b2b;
    --body-ink: #3a3a3a;
    --paper: #ececec;
    --paper-light: #f3f3f3;
    --band-gray: #9a9a9a;
  }
  * { margin: 0; padding: 0; box-sizing: border-box; }
  html, body { width: 960px; height: 1200px; overflow: hidden; background: var(--paper); }
  .letterhead {
    position: relative;
    width: 960px;
    height: 1200px;
    background: linear-gradient(100deg, var(--paper-light) 0%, var(--paper) 45%, #e6e6e6 100%);
    font-family: "Didact Gothic", "Century Gothic", sans-serif;
    color: var(--body-ink);
  }
  .brand {
    position: absolute;
    left: 87px;
    top: 94px;
    font-family: "Poppins", sans-serif;
    font-weight: 700;
    font-size: 24px;
    color: var(--brand-purple);
    display: flex;
    align-items: center;
    gap: 10px;
    letter-spacing: 0.2px;
  }
  .brand-mark {
    width: 14px;
    height: 14px;
    background: var(--brand-purple);
  }
  .contact {
    position: absolute;
    right: 80px;
    top: 112px;
    display: flex;
    font-family: "Poppins", sans-serif;
    font-size: 14px;
    line-height: 17px;
    color: var(--ink);
  }
  .contact-address {
    text-align: right;
    padding-right: 14px;
    border-right: 1.5px solid var(--brand-purple);
  }
  .contact-web { color: var(--brand-purple); font-weight: 500; letter-spacing: 0.5px; }
  .contact-lines { padding-left: 12px; }
  .contact-lines li { list-style: none; display: flex; align-items: center; gap: 6px; }
  .contact-lines svg { width: 10px; height: 10px; fill: var(--brand-purple); }
  .letter {
    position: absolute;
    left: 87px;
    right: 80px;
    top: 350px;
  }
  .salutation {
    font-family: "Poppins", sans-serif;
    font-size: 20px;
    font-weight: 400;
    color: var(--ink);
    margin-bottom: 24px;
  }
  .letter p {
    font-size: 13.2px;
    line-height: 18.3px;
    text-align: justify;
    margin-bottom: 18px;
  }
  .letter .closing { margin-top: 36px; margin-bottom: 22px; }
  .signature {
    width: 124px;
    height: 70px;
    background: linear-gradient(90deg, #d7d7d7, #cfcfcf);
  }
  .footer-band {
    position: absolute;
    left: 0;
    bottom: 0;
    width: 960px;
    height: 10px;
  }
</style>
</head>
<body>
<main class="letterhead">
  <header>
    <div class="brand"><span class="brand-mark"></span>Holloway Realty Group, LLC</div>
    <div class="contact">
      <address class="contact-address" style="font-style:normal">
        4120 Linden Court<br>
        Albany, New York 12208<br>
        <span class="contact-web">www.hollowayrealty.com</span>
      </address>
      <ul class="contact-lines">
        <li><svg viewBox="0 0 10 10"><path d="M2 0.5l1.6 2-0.9 1.2c0.6 1.2 1.4 2 2.6 2.6l1.2-0.9 2 1.6-1 1.8C4 8.5 1.5 6 0.5 1.5z"/></svg>555-014-2280</li>
        <li><svg viewBox="0 0 10 10"><rect x="2.5" y="0.5" width="5" height="3"/><rect x="0.5" y="3.5" width="9" height="4" rx="1"/><rect x="2.5" y="6.5" width="5" height="3"/></svg>555-014-3391</li>
        <li><svg viewBox="0 0 10 10"><path d="M0.5 2h9v6h-9z M0.5 2l4.5 3.5 4.5-3.5" stroke="#ececec" stroke-width="0.8"/></svg>info@hollowayrealty.com</li>
      </ul>
    </div>
  </header>

  <section class="letter">
    <h1 class="salutation">Dear Mr. Carter,</h1>
    <p>Lorem ipsum dolor sit amet, consectetur adipiscing elit. Donec orci purus, luctus vitae dignissim eu, iaculis sed purus. Vivamus faucibus, ipsum nec aliquet viverra, leo mauris condimentum ligula, sit amet sagittis enim ligula quis arcu. Nam egestas tortor id nisi porttitor mattis. In tortor ante, ultricies in suscipit a, tempus non massa. Vivamus et auctor mi. Fusce vel massa nulla. Phasellus nec eros mauris, et scelerisque orci.</p>
    <p>Donec malesuada orci vitae nulla accumsan porta a id massa. Quisque accumsan iaculis magna sit amet fringilla. Maecenas consequat, magna eget tincidunt semper, odio nibh rutrum mi, id feugiat ante nisi eu risus. Vestibulum nunc orci, rhoncus a placerat in, ultricies in mi. Cras mattis varius eros, vel fringilla nisi suscipit eget. Quisque scelerisque sagittis nulla at porttitor.</p>
    <p>Sed id augue vitae urna euismod commodo aliquet a quam. Pellentesque arcu velit, cursus et malesuada ut, consequat et diam. Nullam erat sem, rhoncus id ullamcorper vitae, rhoncus et arcu. In ultricies ultricies nulla, ut rutrum nisi iaculis at. Donec eu magna a metus ornare faucibus. Fusce aliquet faucibus ultricies. Morbi semper, est id tincidunt gravida, sem arcu adipiscing lacus, ac bibendum nulla leo eu purus. Quisque nec diam sed risus consectetur accumsan quis quis nibh. Vestibulum id purus lorem.</p>
    <p>It is a long established fact that a reader will be distracted by the readable content of a page when looking at its layout. The point of using Lorem Ipsum is that it has a more-or-less normal distribution of letters, as opposed to using 'Content here, content here', making it look like readable English. Many desktop publishing packages</p>
    <p class="closing">Sincerely,</p>
    <div class="signature" role="img" aria-label="Handwritten signature of the sender"></div>
  </section>

  <svg class="footer-band" viewBox="0 0 960 10" preserveAspectRatio="none" aria-hidden="true">
    <rect x="0" y="0" width="960" height="10" fill="var(--band-gray)"/>
    <polygon points="0,0 788,0 797,10 0,10" fill="var(--brand-purple)"/>
    <polygon points="788,0 792,0 801,10 797,10" fill="#ececec"/>
  </svg>
</main>
</body>
</html>
```